Website Homepage for Gulfward Crestline Labs

Website is a white label new branding of this product:
https://www.roofbrillo.example

Looking for home page / landing page design.

The focus should be on its characteristics that showcase its ability to protect your roof from hurricanes and weather. Focus is only on the roof use case.

Helps restore original color
Bonds shingle granules
Penetrates and rejuvenates
Extend your roofs life
Prevents mold, mildew and moss growth
FrostGuard Colors are heat reflective and UV resistance
Environmentally Friendly
Added flexibility
Added Impact Resistance
Added Wind Resistance
Heat reflective
Reflect harmful UV rays
Reduce energy consumption
Extend the life of the shingle
Stop mold, mildew and algae from growing again!
Built it mildicide, moldicide, and algaecide.

Some other consideration marketing ideas to portray:

Roof replacement alternative with $0 down financing

Don’t replace, rejuvenate!

Stop! Before replacing your roof look at this solution…. With our advanced technology spray and seal coatings you can have a rejuvenated roof that is better than a new one! At a fraction of the cost!

Repel wind, repel water and repel impact. Make your roof stronger than ever.

Is your roof ready for hurricane season? What if there was a simple 1 day application coating that could help you to strengthen your roof against wind, rain and impact?

Self insured home? Protect your roof with our rejuvenating roof coatings that extend the life of your roof by 15+ years.

Have you recently installed a roof? Don’t wait for the next hurricane to damage it. Protect it today with our sealant coatings that repel wind, water and impact!

Ready for a new roof but don’t have the budget. Use our colored coatings that not only make your roof new again, but can also recolor it!

The sun is damaging your roof every day! Our coatings protect it from UV damage as well as water, wind, and impact!

Have a tile or clay roof? Tired of algae, mold and mildew growing on your roof? We will clean your roof and prevent regrowth in the future with our coatings!

Industry/Entity Type

Construction

Number of Pages Required

1 page

Font styles to use
Sans Serif

Colors
0054AA
0677BA
7BADD7
CADEEF
E8F1F8
0094D4
00A9DD
6FCCEA
C7EBF8
E9F6FB

Requirements
Nice to have
• Modern blue / grey / black color scheme. Not a lot of white space.

```html
<!DOCTYPE html>
<html lang="en">
<head>
<meta charset="utf-8">
<title>Gulfward Crestline – Roof Protection</title>
<link href="https://fonts.googleapis.com/css2?family=Poppins:wght@400;500;600;700&display=swap" rel="stylesheet">
<style>
:root{
  --black:#000;
  --ink:#0a0f1c;
  --navy:#0c2b4f;
  --navy-deep:#0d2c54;
  --blue:#1a8cf0;
  --blue-bright:#2196f3;
  --blue-dark:#0054aa;
  --blue-soft:#7badd7;
  --field:#e8e8e8;
  --white:#fff;
  --grey:#b8c0cc;
  --muted:#8a94a3;
}
*{box-sizing:border-box;margin:0;padding:0}
html,body{width:1200px;height:5165px;overflow:hidden;background:var(--black);font-family:'Poppins',sans-serif;color:var(--white)}
.page{position:relative;width:1200px;height:5165px}
.abs{position:absolute}
.btn{position:absolute;display:flex;align-items:center;justify-content:center;background:var(--blue);color:var(--white);font-size:18px;font-weight:500;text-transform:uppercase}
.btn-outline{border:2px solid var(--white)}
h2.section-title{position:absolute;left:0;width:1200px;text-align:center;font-size:28px;font-weight:600;text-transform:uppercase}
.photo{position:absolute}

/* top bar */
.topbar{position:absolute;top:0;left:0;width:1200px;height:36px;background:var(--ink);font-size:13px;display:flex;align-items:center;gap:56px;padding-left:24px}
.topbar span{display:flex;align-items:center;gap:10px}
.nav{position:absolute;top:36px;left:0;width:1200px;height:80px;background:var(--black)}
.brand{position:absolute;display:flex;align-items:center;gap:8px;font-weight:700;text-transform:uppercase;line-height:1.05;color:var(--white)}
.brand .dot{width:14px;height:14px;background:var(--blue);border-radius:50%}
.nav-links{position:absolute;top:32px;left:275px;display:flex;gap:0;font-size:18px;font-weight:500}
.nav-links a{color:var(--white);text-decoration:none;position:absolute;white-space:nowrap}

/* hero */
.hero{position:absolute;top:116px;left:0;width:1200px;height:580px;background:linear-gradient(160deg,#3b4a3c 0%,#495652 35%,#3a424c 65%,#2a3038 100%)}
.hero-title{position:absolute;left:16px;top:148px;font-size:37px;font-weight:700;line-height:1.2;text-transform:uppercase}
.hero-sub{position:absolute;left:20px;top:248px;width:520px;font-size:12px;line-height:1.95;text-transform:uppercase}
.play{position:absolute;left:858px;top:168px}

/* strengths */
.strong-title{position:absolute;left:44px;top:752px;font-size:27px;font-weight:600;line-height:1.25;text-transform:uppercase}
.strength{position:absolute;top:860px;width:150px;text-align:center;font-size:18px}
.strength svg{display:block;margin:0 auto 20px}

/* quote form */
.quote{position:absolute;left:646px;top:432px;width:502px;height:620px;background:var(--navy)}
.quote h3{position:absolute;top:44px;left:0;width:100%;text-align:center;font-size:27px;font-weight:600;text-transform:uppercase}
.field{position:absolute;height:36px;background:var(--field);color:#9aa0a8;font-size:10px;padding:12px 14px;text-transform:uppercase;border-bottom:2px solid #cfd3d8}

/* about */
.badge{position:absolute;left:366px;top:1480px;width:196px;height:196px;border-radius:50%;background:var(--blue);text-align:center}
.badge b{display:block;font-size:62px;font-weight:600;line-height:1;margin-top:42px}
.badge span{display:block;font-size:17px;line-height:1.3}
.about-title{position:absolute;left:640px;top:1248px;font-size:27px;font-weight:600;line-height:1.25;text-transform:uppercase}
.about-text{position:absolute;left:640px;top:1358px;width:490px;font-size:15px;line-height:1.4}

/* features */
.features{position:absolute;top:1812px;left:0;width:1200px;height:836px;background:linear-gradient(135deg,#1d2d44 0%,#1f3a60 45%,#1f4a80 100%)}
.feature{position:absolute;width:240px;text-align:center;font-size:18px;line-height:1.35}
.feature .ic{width:96px;height:96px;border-radius:50%;background:var(--blue);border:3px solid #cfe6fb;margin:0 auto 16px;display:flex;align-items:center;justify-content:center}

/* cta */
.cta{position:absolute;top:3536px;left:0;width:1200px;height:294px}
.cta h3{position:absolute;left:44px;top:78px;font-size:30px;font-weight:600;text-transform:uppercase}
.cta p{position:absolute;left:44px;top:124px;width:500px;font-size:20px;line-height:1.3}

/* testimonials */
.card{position:absolute;top:4046px;width:334px;height:170px;background:var(--white);color:#8a8f96;font-size:13px;line-height:1.6;padding:36px 16px 0}
.person{position:absolute;top:4240px;display:flex;align-items:center;gap:20px}
.person .av{width:60px;height:60px;border-radius:50%;background:linear-gradient(135deg,#b9a48c,#5a4c40)}
.person b{display:block;color:#6d7f95;font-size:14px;font-weight:500}
.person span{display:block;color:var(--blue);font-size:10px;font-weight:600}

/* as seen on */
.seen{position:absolute;top:4385px;left:0;width:1200px;height:320px;background:var(--white)}
.seen h2{color:var(--blue-dark);top:78px;font-size:27px}
.media{position:absolute;top:158px;height:60px;border-radius:6px;background:#d6dde6}

/* footer */
.footer-col h4{font-size:20px;font-weight:600;color:var(--blue);text-transform:uppercase;margin-bottom:20px}
.footer-col a{display:block;color:var(--white);text-decoration:none;font-size:16px;text-transform:uppercase;margin-bottom:25px}
.footer-col a::before{content:"›";color:var(--blue);margin-right:10px}
.contact{position:absolute;left:46px;font-size:16px;display:flex;gap:16px;line-height:1.25}
.social{position:absolute;top:5026px;width:30px;height:30px;border-radius:50%;background:var(--blue)}
.copyright{position:absolute;top:5118px;font-size:12px;font-weight:500;text-transform:uppercase}
</style>
</head>
<body>
<div class="page">

  <!-- top bar -->
  <div class="topbar">
    <span><svg width="14" height="14" viewBox="0 0 24 24"><path d="M12 2a7 7 0 0 0-7 7c0 5 7 13 7 13s7-8 7-13a7 7 0 0 0-7-7zm0 9.5a2.5 2.5 0 1 1 0-5 2.5 2.5 0 0 1 0 5z" fill="#fff"/></svg>2250 Harbor Point Drive, Suite 200</span>
    <span style="margin-left:80px"><svg width="14" height="14" viewBox="0 0 24 24"><path d="M6.6 10.8a15 15 0 0 0 6.6 6.6l2.2-2.2a1 1 0 0 1 1-.25 11.4 11.4 0 0 0 3.6.57 1 1 0 0 1 1 1V20a1 1 0 0 1-1 1A17 17 0 0 1 3 4a1 1 0 0 1 1-1h3.5a1 1 0 0 1 1 1c0 1.25.2 2.45.57 3.57a1 1 0 0 1-.25 1z" fill="var(--blue)"/></svg>(800) 555-0142</span>
  </div>

  <!-- nav -->
  <header class="nav">
    <div class="brand" style="left:22px;top:22px;font-size:15px"><div>Gulfward<br>Crestline</div><div class="dot"></div></div>
    <nav class="nav-links">
      <a style="left:0">HOME</a>
      <a style="left:100px">ABOUT</a>
      <a style="left:219px">SERVICES</a>
      <a style="left:359px">GALLERY</a>
      <a style="left:493px">TESTIMONIALS</a>
    </nav>
    <div class="btn" style="left:970px;top:22px;width:200px;height:40px">Get a Quote</div>
  </header>

  <!-- hero -->
  <section class="hero" role="img" aria-label="Crew member spraying sealant coating on a shingle roof">
    <h1 class="hero-title">Protect your roof from<br>hurricanes and weather</h1>
    <p class="hero-sub">With our advanced technology spray and seal coatings you can have a rejuvenated roof that is better than a new one! At a fraction of the cost!</p>
    <div class="btn" style="left:20px;top:334px;width:198px;height:40px">Get a Quote</div>
    <svg class="play" width="100" height="100" viewBox="0 0 100 100"><circle cx="50" cy="50" r="46" fill="var(--blue)" stroke="#c7d6e6" stroke-width="6"/><path d="M40 30v40l32-20z" fill="#fff"/></svg>
  </section>

  <!-- strengths -->
  <h2 class="strong-title">Make your roof stronger<br>than ever.</h2>
  <div class="strength" style="left:34px">
    <svg width="100" height="100" viewBox="0 0 100 100" fill="none" stroke="var(--blue)" stroke-width="3"><path d="M10 20h30M8 30h26M12 40h20"/><path d="M20 90l15-40h55l-15 40z"/><path d="M30 70h52M42 50l-10 40M58 50l-10 40M74 50l-10 40"/><rect x="55" y="28" width="16" height="20"/></svg>
    Repel Wind
  </div>
  <div class="strength" style="left:232px">
    <svg width="100" height="100" viewBox="0 0 100 100" fill="none" stroke="var(--blue)" stroke-width="3"><path d="M36 30a12 12 0 0 1 24-6 10 10 0 0 1 6 19H36a7 7 0 0 1 0-13z"/><path d="M42 50v8M52 50v8M62 50v8"/><path d="M15 92l35-30 35 30z"/><path d="M28 80h44"/></svg>
    Repel Water
  </div>
  <div class="strength" style="left:446px">
    <svg width="100" height="100" viewBox="0 0 100 100" fill="none" stroke="var(--blue)" stroke-width="3"><circle cx="34" cy="28" r="14"/><path d="M26 28h16M34 20v16"/><path d="M30 90l14-38h46l-14 38z"/><path d="M37 71h46M52 52l-14 38M68 52l-14 38"/></svg>
    Repel Impact
  </div>

  <!-- quote form -->
  <aside class="quote">
    <h3>10% Off Roof Protection</h3>
    <div class="field" style="left:29px;top:120px;width:210px">First Name</div>
    <div class="field" style="left:262px;top:120px;width:210px">Last Name</div>
    <div class="field" style="left:29px;top:180px;width:443px">Email Address</div>
    <div class="field" style="left:29px;top:240px;width:443px">Phone Number</div>
    <div class="field" style="left:29px;top:296px;width:443px">Address</div>
    <div class="field" style="left:29px;top:358px;width:210px">City</div>
    <div class="field" style="left:262px;top:358px;width:210px">State</div>
    <div class="field" style="left:29px;top:416px;width:443px">Project</div>
    <div class="btn" style="left:154px;top:524px;width:196px;height:40px">Get a Quote</div>
  </aside>

  <!-- about -->
  <div class="photo" style="left:42px;top:1196px;width:543px;height:419px;background:linear-gradient(180deg,#9aa3ad 0%,#b7bec6 40%,#6f7b86 62%,#5d6a52 100%)" role="img" aria-label="Two-storey house with a freshly coated shingle roof"></div>
  <div class="badge"><b>10+</b><span>Years Of<br>Experience</span></div>
  <h2 class="about-title">Is your roof ready for<br>hurricane season?.</h2>
  <p class="about-text">What if there was a simple 1 day application coating that could help you to strengthen your roof against wind, rain and impact. The sun is damaging your roof every day! Our coatings protect it from UV damage as well as water, wind, and impact!</p>
  <div class="btn" style="left:640px;top:1482px;width:198px;height:40px">More About Us</div>

  <!-- features -->
  <section class="features" role="img" aria-label="Close view of shingle roof texture in blue tones">
    <h2 class="section-title" style="top:98px;line-height:1.2">Our coatings protect it from UV damage<br>as well as water, wind, and impact!</h2>
    <div class="feature" style="left:110px;top:240px"><div class="ic"><svg width="48" height="48" viewBox="0 0 48 48" fill="none" stroke="#fff" stroke-width="2.5"><rect x="10" y="14" width="22" height="26" rx="2"/><path d="M10 20h22M32 22l8-6v14"/></svg></div>Helps restore<br>original color</div>
    <div class="feature" style="left:338px;top:248px"><div class="ic"><svg width="48" height="48" viewBox="0 0 48 48" fill="none" stroke="#fff" stroke-width="2.5"><circle cx="24" cy="24" r="5"/><path d="M24 6v10M24 32v10M6 24h10M32 24h10M11 11l7 7M30 30l7 7M37 11l-7 7M18 30l-7 7"/></svg></div>Bonds shingle<br>granules</div>
    <div class="feature" style="left:590px;top:248px"><div class="ic"><svg width="48" height="48" viewBox="0 0 48 48" fill="none" stroke="#fff" stroke-width="2.5"><path d="M6 34l8-18h28l-8 18z"/><path d="M10 25h28M20 16l-8 18M28 16l-8 18M36 16l-8 18"/></svg></div>Extend your<br>roofs life</div>
    <div class="feature" style="left:850px;top:240px"><div class="ic"><svg width="48" height="48" viewBox="0 0 48 48" fill="none" stroke="#fff" stroke-width="2.5"><circle cx="16" cy="16" r="4"/><circle cx="32" cy="14" r="3"/><circle cx="24" cy="28" r="5"/><circle cx="36" cy="32" r="3"/><circle cx="12" cy="34" r="3"/></svg></div>Prevents mold, mildew<br>and moss growth</div>
    <div class="feature" style="left:110px;top:460px"><div class="ic"><svg width="48" height="48" viewBox="0 0 48 48" fill="none" stroke="#fff" stroke-width="2.5"><circle cx="24" cy="24" r="16"/><path d="M14 16c6 2 6 8 12 8s4 10 10 8M30 36c0-6 4-8 8-8"/></svg></div>Environmentally<br>Friendly</div>
    <div class="feature" style="left:338px;top:468px"><div class="ic"><svg width="48" height="48" viewBox="0 0 48 48" fill="none" stroke="#fff" stroke-width="2.5"><circle cx="24" cy="24" r="8"/><path d="M24 6v6M24 36v6M6 24h6M36 24h6M11 11l4 4M33 33l4 4M37 11l-4 4M15 33l-4 4"/></svg></div>Heat reflective</div>
    <div class="feature" style="left:590px;top:468px"><div class="ic"><svg width="48" height="48" viewBox="0 0 48 48" fill="none" stroke="#fff" stroke-width="2.5"><path d="M6 18h26a5 5 0 1 0-5-5M6 26h34a5 5 0 1 1-5 5M10 34h14"/></svg></div>Added Wind<br>Resistance</div>
    <div class="feature" style="left:850px;top:460px"><div class="ic"><svg width="48" height="48" viewBox="0 0 48 48" fill="none" stroke="#fff" stroke-width="2.5"><path d="M40 24a16 16 0 1 1-5-11.6"/><path d="M36 6v8h-8"/><path d="M24 14v10l7 5"/></svg></div>Extend the life of<br>the shingle</div>
    <div class="btn btn-outline" style="left:496px;top:702px;width:200px;height:42px">View More</div>
  </section>

  <!-- recent work -->
  <h2 class="section-title" style="top:2706px">Our Recent Work</h2>
  <div class="photo" style="left:42px;top:2820px;width:592px;height:248px;background:linear-gradient(180deg,#8f99a4 0%,#6d7784 50%,#c9c2b0 100%)" role="img" aria-label="Coated roof over a house with a white garage door"></div>
  <div class="photo" style="left:648px;top:2820px;width:500px;height:248px;background:linear-gradient(180deg,#9fb0bf 0%,#5f6a58 35%,#6e7378 100%)" role="img" aria-label="Wide view of a sealed shingle roof"></div>
  <div class="photo" style="left:42px;top:3086px;width:356px;height:250px;background:linear-gradient(160deg,#9aa7b3 0%,#7e8a72 50%,#4a5a48 100%)" role="img" aria-label="Worker in safety harness on a roof"></div>
  <div class="photo" style="left:416px;top:3086px;width:356px;height:250px;background:linear-gradient(160deg,#5e6268 0%,#7c8087 50%,#a7a9ac 100%)" role="img" aria-label="Worker spraying coating across shingles"></div>
  <div class="photo" style="left:790px;top:3086px;width:358px;height:250px;background:linear-gradient(170deg,#3f6b3a 0%,#5f8a4e 50%,#6a6e72 100%)" role="img" aria-label="Crew member coating a roof beside pine trees"></div>
  <div class="btn btn-outline" style="left:500px;top:3400px;width:200px;height:42px">View Gallery</div>

  <!-- cta band -->
  <section class="cta">
    <div class="abs" style="left:0;top:0;width:1200px;height:294px;background:linear-gradient(150deg,#4d5a52,#39433f 60%,#2d3338)" role="img" aria-label="Crew member spraying a roof on a rural property"></div>
    <svg class="abs" style="left:0;top:0" width="640" height="294"><polygon points="0,0 632,0 512,294 0,294" fill="var(--blue-bright)"/></svg>
    <h3>Have a tile or clay roof?</h3>
    <p>We will clean your roof and prevent regrowth in the future with our coatings!</p>
    <div class="btn" style="left:44px;top:200px;width:218px;height:44px;background:var(--navy-deep)">Get a Quote</div>
  </section>

  <!-- testimonials -->
  <h2 class="section-title" style="top:3928px;font-size:30px">What Customer Say’s</h2>
  <div class="card" style="left:60px">Our shingles look new again and the crew finished in one day. The coating held firm through the last storm season.</div>
  <div class="card" style="left:432px">Our shingles look new again and the crew finished in one day. The coating held firm through the last storm season.</div>
  <div class="card" style="left:808px">Our shingles look new again and the crew finished in one day. The coating held firm through the last storm season.</div>
  <div class="person" style="left:86px"><div class="av" role="img" aria-label="Customer portrait"></div><div><b>Dana R. Holloway</b><span>CUSTOMER</span></div></div>
  <div class="person" style="left:458px"><div class="av" role="img" aria-label="Customer portrait"></div><div><b>Dana R. Holloway</b><span>CUSTOMER</span></div></div>
  <div class="person" style="left:846px"><div class="av" role="img" aria-label="Customer portrait"></div><div><b>Dana R. Holloway</b><span>CUSTOMER</span></div></div>

  <!-- as seen on -->
  <section class="seen">
    <h2 class="section-title">As Seen On?</h2>
    <div class="media" style="left:50px;width:180px"></div>
    <div class="media" style="left:284px;width:176px"></div>
    <div class="media" style="left:512px;width:178px"></div>
    <div class="media" style="left:742px;width:176px"></div>
    <div class="media" style="left:972px;width:172px"></div>
  </section>

  <!-- footer -->
  <div class="brand" style="left:50px;top:4810px;font-size:20px"><div>Gulfward<br>Crestline</div><div class="dot"></div></div>
  <div class="contact" style="top:4894px"><svg width="20" height="20" viewBox="0 0 24 24"><path d="M6.6 10.8a15 15 0 0 0 6.6 6.6l2.2-2.2a1 1 0 0 1 1-.25 11.4 11.4 0 0 0 3.6.57 1 1 0 0 1 1 1V20a1 1 0 0 1-1 1A17 17 0 0 1 3 4a1 1 0 0 1 1-1h3.5a1 1 0 0 1 1 1c0 1.25.2 2.45.57 3.57a1 1 0 0 1-.25 1z" fill="var(--blue)"/></svg>(800) 555-0142</div>
  <div class="contact" style="top:4932px"><svg width="20" height="20" viewBox="0 0 24 24"><path d="M12 2a7 7 0 0 0-7 7c0 5 7 13 7 13s7-8 7-13a7 7 0 0 0-7-7zm0 9.5a2.5 2.5 0 1 1 0-5 2.5 2.5 0 0 1 0 5z" fill="var(--blue)"/></svg><span>2250 Harbor Point Drive,<br>Suite 200 Tampa, Florida<br>33602 United States</span></div>
  <div class="social" style="left:72px"></div>
  <div class="social" style="left:124px"></div>
  <div class="social" style="left:176px"></div>

  <div class="footer-col abs" style="left:367px;top:4790px"><h4>Sealers</h4><a>Roof Sealers</a><a>Roof Coatings</a><a>Energy Efficient Roof</a><a>Roof Facts</a></div>
  <div class="footer-col abs" style="left:678px;top:4790px"><h4>Company</h4><a>Home</a><a>About</a><a>Gallery</a><a>Contact</a></div>
  <div class="footer-col abs" style="left:910px;top:4790px"><h4>Gulfward Crestline</h4><a>FAQs</a><a>Test Videos</a><a>Video Gallery</a><a>Get a Quote</a></div>

  <div class="abs" style="left:24px;top:5092px;width:1152px;height:2px;background:var(--blue)"></div>
  <div class="copyright" style="left:24px">© All rights reserved by Gulfward Crestline</div>
  <div class="copyright" style="right:24px">Privacy Policy | Term and Conditions</div>

</div>
</body>
</html>
```